Refresh Application User Interface

Brightmoor wishes to update the look of its business applications. Two representative forms are shown below. Please note, we are not considering changes in functionality or usability. Our goal is a cleaner, more contemporary design.

Industry/Entity Type

Business

```html
<!DOCTYPE html>
<html lang="en">
<head>
<meta charset="utf-8">
<title>Brightmoor – Purchase Order Lines</title>
<link href="https://fonts.googleapis.com/css2?family=Hind:wght@300;400;500;600&display=swap" rel="stylesheet">
<style>
:root{
  --topbar:#3b3b3b;
  --topbar-active:#c9c9c9;
  --blue:#3f8de6;
  --blue-dark:#1e4f9c;
  --page:#ebebeb;
  --panel:#ffffff;
  --section:#f5f5f5;
  --green:#4fcf8c;
  --text:#444;
  --muted:#7b8794;
  --label:#8a8a8a;
  --field:#f7f7f7;
  --field-border:#d6d6d6;
  --red:#e2364a;
}
*{box-sizing:border-box;margin:0;padding:0}
html,body{width:1200px;height:756px;overflow:hidden}
body{font-family:"Hind",sans-serif;background:var(--page);color:var(--text);position:relative}
.abs{position:absolute}
/* top bar */
.topbar{left:0;top:0;width:1200px;height:32px;background:var(--topbar);color:#fff}
.user{left:14px;top:7px;font-size:15px;font-weight:500}
.gear{left:97px;top:9px}
.role{left:149px;top:9px;font-size:13px;font-weight:600}
.toplink{top:0;height:32px;line-height:34px;font-size:11.5px;color:#e6e6e6;text-align:center}
.toplink.active{background:var(--topbar-active);color:#555}
/* modules */
.modules{left:0;top:32px;width:1200px;height:41px;background:#fff}
.module{top:0;height:41px;line-height:44px;font-size:11px;color:#777;text-align:center;border-right:1px solid #e4e4e4}
.module.active{background:var(--blue);color:#fff;font-weight:600;border-right:none}
.brand{left:1022px;top:40px;font-size:25px;font-weight:600;color:var(--blue-dark);letter-spacing:1px}
/* sub nav */
.subnav{left:0;top:73px;width:1200px;height:29px;background:var(--blue)}
.subitem{top:80px;font-size:10.5px;color:#fff;font-weight:500;transform:translateX(-50%)}
.subitem.current{font-weight:600}
.underline{left:199px;top:97px;width:82px;height:2px;background:#fff}
.sep{left:455px;top:79px;width:1px;height:15px;background:#fff}
/* title & tabs */
.title{left:149px;top:127px;font-size:20px;font-weight:400;color:var(--muted);letter-spacing:.3px}
.htab{top:126px;height:32px;line-height:36px;font-size:13px;text-align:center;color:#888;background:#fff;border:1px solid #e0e0e0;border-bottom:none}
.htab.active{top:118px;height:40px;line-height:42px;background:var(--blue);color:#fff;border:none;font-weight:500}
/* panel */
.panel{left:149px;top:158px;width:902px;height:544px;background:var(--panel);box-shadow:0 1px 3px rgba(0,0,0,.12)}
.toolbar-strip{left:149px;top:158px;width:8px;height:30px;background:var(--green)}
.toolbar-line{left:157px;top:187px;width:894px;height:1px;background:#e6e6e6}
.tool{top:166px}
.tooldiv{left:360px;top:164px;width:1px;height:18px;background:#ddd}
.post{left:376px;top:166px;font-size:11px;color:#444;display:flex;align-items:center;gap:5px}
.tip{left:154px;top:189px;width:92px;height:19px;background:var(--green);color:#fff;font-size:10px;font-weight:500;text-align:center;line-height:21px;border-radius:2px}
.tip::before{content:"";position:absolute;left:36px;top:-5px;border:5px solid transparent;border-top:none;border-bottom-color:var(--green)}
.lbl{font-size:13px;color:var(--label);font-weight:500;text-align:right}
.val{font-size:13px;color:var(--label);font-weight:500}
.input{height:22px;border:1px solid var(--field-border);background:var(--field);font-size:11.5px;padding:4px 8px 0;color:#444}
.slash{font-size:15px;color:#888}
.accept{left:922px;top:290px;font-size:11px;color:#777;display:flex;align-items:center;gap:4px}
.box{width:13px;height:13px;border:1px solid #888;background:#fff;position:relative}
.link{left:922px;top:338px;font-size:11px;color:#777;border-bottom:1px solid #888}
/* section tabs */
.stab{top:401px;height:25px;line-height:28px;background:var(--blue);color:#fff;font-size:11.5px;font-weight:500;text-align:center}
.stab.active{top:395px;height:32px;line-height:34px;background:#fff;color:#888;font-size:13px;font-weight:400;border:1px solid #ddd;border-bottom:none}
.section{left:149px;top:426px;width:902px;height:276px;background:var(--section)}
.flbl{font-size:9.5px;color:#555}
.select{height:21px;background:#fff;box-shadow:0 1px 1px rgba(0,0,0,.18);font-size:11.5px;color:#666;padding:3px 9px 0}
.select::after{content:"";position:absolute;right:9px;top:9px;border:4px solid transparent;border-top:5px solid #888;border-bottom:none}
.req{color:var(--red);font-size:12px}
.plain{height:21px;background:#fff;box-shadow:0 1px 1px rgba(0,0,0,.18)}
.grey{height:21px;background:#e8e8e8;border:1px solid #d5d5d5}
/* status */
.status{left:149px;top:714px;width:902px;height:26px;background:#fff}
.status-strip{left:149px;top:714px;width:8px;height:26px;background:var(--green)}
.status-text{left:174px;top:720px;font-size:11px;color:#555;display:flex;align-items:center;gap:3px}
</style>
</head>
<body>

<header>
  <div class="abs topbar"></div>
  <div class="abs user">Dana Reyes</div>
  <svg class="abs gear" width="16" height="16" viewBox="0 0 16 16"><circle cx="8" cy="8" r="5.2" fill="none" stroke="#fff" stroke-width="3" stroke-dasharray="2.2 1.4"/><circle cx="8" cy="8" r="4" fill="#fff"/><circle cx="8" cy="8" r="1.8" fill="var(--topbar)"/></svg>
  <div class="abs role">Administrator
    <svg width="10" height="8" viewBox="0 0 10 8" style="margin-left:3px"><path d="M1 2l4 4 4-4" fill="none" stroke="#fff" stroke-width="1.6"/></svg>
  </div>
  <div class="abs toplink" style="left:842px;width:72px">TOUCH</div>
  <div class="abs toplink active" style="left:914px;width:82px">NEW TAB</div>
  <div class="abs toplink" style="left:996px;width:62px">HELP</div>
  <div class="abs toplink" style="left:1058px;width:84px">SUPPORT</div>
  <svg class="abs" style="left:1170px;top:9px" width="18" height="15" viewBox="0 0 18 15"><path d="M1 1h7v13H1z" fill="none" stroke="#fff" stroke-width="1.5"/><path d="M9 7.5h8M14 4.5l3 3-3 3" fill="none" stroke="#fff" stroke-width="1.5"/></svg>

  <nav>
    <div class="abs modules"></div>
    <div class="abs module" style="left:0;width:86px;top:32px">Home</div>
    <div class="abs module" style="left:86px;width:93px;top:32px">eSource</div>
    <div class="abs module active" style="left:179px;width:79px;top:32px">eBuy</div>
    <div class="abs module" style="left:258px;width:100px;top:32px">eRequest</div>
    <div class="abs module" style="left:358px;width:76px;top:32px">eSell</div>
    <div class="abs module" style="left:434px;width:86px;top:32px">eStock</div>
    <div class="abs module" style="left:520px;width:80px;top:32px">ePlan</div>
    <div class="abs module" style="left:600px;width:108px;top:32px">Preferences</div>
    <div class="abs brand">BRIGHTMOOR</div>

    <div class="abs subnav"></div>
    <div class="abs subitem current" style="left:240px">Orders</div>
    <div class="abs underline"></div>
    <div class="abs subitem" style="left:324px">Recipients</div>
    <div class="abs subitem" style="left:412px">Shipments</div>
    <div class="abs sep"></div>
    <div class="abs subitem" style="left:493px">Invoices</div>
    <div class="abs subitem" style="left:574px">Pricing</div>
    <div class="abs subitem" style="left:643px">Tables</div>
    <div class="abs subitem" style="left:714px">Reports</div>
    <div class="abs subitem" style="left:790px">Inquiries</div>
    <div class="abs subitem" style="left:881px">Periodic Tasks</div>
    <div class="abs subitem" style="left:974px">Workflows</div>
  </nav>
</header>

<main>
  <h1 class="abs title">PURCHASE ORDER LINES</h1>
  <div class="abs htab active" style="left:712px;width:94px">HEADER</div>
  <div class="abs htab" style="left:806px;width:81px">LINES</div>
  <div class="abs htab" style="left:888px;width:81px">CHARGES</div>
  <div class="abs htab" style="left:970px;width:81px">NOTES</div>
  <svg class="abs" style="left:1033px;top:131px" width="12" height="12" viewBox="0 0 12 12"><circle cx="6" cy="6" r="6" fill="var(--green)"/><path d="M3 6.2l2 2 4-4" fill="none" stroke="#fff" stroke-width="1.5"/></svg>

  <section class="abs panel"></section>
  <div class="abs toolbar-strip"></div>
  <div class="abs toolbar-line"></div>
  <svg class="abs tool" style="left:180px" width="14" height="14" viewBox="0 0 14 14"><path d="M9 4L4.5 8.5a1.5 1.5 0 0 0 2 2L11 6a3 3 0 0 0-4-4L2.5 6.5a4.2 4.2 0 0 0 6 6L12 9" fill="none" stroke="var(--green)" stroke-width="1.3"/></svg>
  <svg class="abs tool" style="left:217px" width="14" height="14" viewBox="0 0 14 14"><path d="M1 5l5-4 5 5-4 5z" fill="none" stroke="#333" stroke-width="1.4"/><circle cx="10" cy="10" r="2.5" fill="none" stroke="#333" stroke-width="1.4"/></svg>
  <svg class="abs tool" style="left:255px" width="14" height="14" viewBox="0 0 14 14"><path d="M3 10L7 4l5 4" stroke="#333" fill="none"/><circle cx="3" cy="10" r="2.2" fill="#333"/><circle cx="7" cy="4" r="2.2" fill="#333"/><circle cx="12" cy="8" r="1.8" fill="#333"/></svg>
  <svg class="abs tool" style="left:292px" width="14" height="14" viewBox="0 0 14 14"><rect x="1" y="4" width="12" height="9" rx="1" fill="#333"/><rect x="4.5" y="1.5" width="5" height="3" fill="none" stroke="#333" stroke-width="1.3"/><rect x="1" y="7.5" width="12" height="1" fill="#fff"/></svg>
  <svg class="abs tool" style="left:329px" width="13" height="13" viewBox="0 0 13 13"><circle cx="6.5" cy="6.5" r="6.5" fill="#ccc"/><text x="6.5" y="10" font-size="9" text-anchor="middle" fill="#fff" font-family="Hind,sans-serif" font-weight="600">?</text></svg>
  <div class="abs tooldiv"></div>
  <div class="abs post"><svg width="12" height="12" viewBox="0 0 12 12"><rect width="12" height="12" rx="1" fill="#333"/><path d="M6 3v6M3 6h6" stroke="#fff" stroke-width="1.5"/></svg>Post Order</div>
  <svg class="abs tool" style="left:902px" width="13" height="14" viewBox="0 0 13 14"><circle cx="5.5" cy="5.5" r="4.5" fill="none" stroke="#ccc" stroke-width="2"/><path d="M8.5 9l3.5 4" stroke="#ccc" stroke-width="2.2"/></svg>
  <svg class="abs tool" style="left:932px" width="12" height="12" viewBox="0 0 12 12"><path d="M6 0v12M0 6h12" stroke="#ccc" stroke-width="2.2"/></svg>
  <svg class="abs tool" style="left:961px" width="15" height="12" viewBox="0 0 15 12"><path d="M1 6l4.5 4.5L14 1" fill="none" stroke="#3dbb6c" stroke-width="2.4"/></svg>
  <svg class="abs tool" style="left:993px" width="11" height="11" viewBox="0 0 11 11"><path d="M1 1l9 9M10 1l-9 9" stroke="#e02424" stroke-width="2.4"/></svg>
  <svg class="abs tool" style="left:1021px" width="13" height="12" viewBox="0 0 13 12"><path d="M4 1L1 3.5 4 6M1.5 3.5h6a4 4 0 0 1 0 8H3" fill="none" stroke="#3dbb6c" stroke-width="1.8"/></svg>
  <div class="abs tip">Attachments</div>

  <div class="abs lbl" style="left:190px;width:71px;top:219px">Order #</div>
  <div class="abs val" style="left:274px;top:219px">100159</div>

  <div class="abs lbl" style="left:180px;width:81px;top:265px">Ship From</div>
  <div class="abs input" style="left:271px;top:262px;width:119px">1001</div>
  <div class="abs slash" style="left:402px;top:262px">/</div>
  <div class="abs input" style="left:418px;top:262px;width:43px">0</div>
  <div class="abs input" style="left:271px;top:286px;width:296px">Harbor Clinical Co.</div>
  <div class="abs lbl" style="left:180px;width:81px;top:315px">Address</div>
  <div class="abs input" style="left:271px;top:311px;width:296px">18 Linden Street</div>
  <div class="abs input" style="left:271px;top:336px;width:296px"></div>

  <div class="abs lbl" style="left:594px;width:80px;top:265px">City</div>
  <div class="abs input" style="left:686px;top:261px;width:219px">Westbrook</div>
  <div class="abs lbl" style="left:594px;width:80px;top:289px">State</div>
  <div class="abs input" style="left:686px;top:286px;width:219px">MA</div>
  <div class="abs lbl" style="left:594px;width:80px;top:315px">Country</div>
  <div class="abs input" style="left:686px;top:311px;width:219px">United States</div>
  <div class="abs lbl" style="left:594px;width:80px;top:339px">ZIP</div>
  <div class="abs input" style="left:686px;top:336px;width:219px">01962-4410</div>
  <div class="abs accept"><span class="box"><svg class="abs" style="left:1px;top:-2px" width="12" height="13" viewBox="0 0 12 13"><path d="M1 7l3 3 7-9" fill="none" stroke="#333" stroke-width="1.3"/></svg></span>Accept</div>
  <div class="abs link">Add Contact</div>

  <div class="abs stab" style="left:150px;width:138px">ORDER INFO</div>
  <div class="abs section"></div>
  <div class="abs stab active" style="left:290px;width:136px">SHIPPING</div>
  <div class="abs stab" style="left:428px;width:138px">PAYMENT</div>
  <div class="abs stab" style="left:567px;width:138px">ACCOUNTS</div>
  <div class="abs stab" style="left:706px;width:139px">TOTALS / APPROVAL</div>

  <div class="abs flbl" style="left:256px;top:443px">Receive At</div>
  <div class="abs select" style="left:256px;top:456px;width:154px">ALCH</div>
  <div class="abs req" style="left:418px;top:458px">*</div>
  <div class="abs flbl" style="left:256px;top:483px">Carrier</div>
  <div class="abs select" style="left:256px;top:496px;width:154px">Swiftline</div>
  <div class="abs req" style="left:418px;top:498px">*</div>
  <div class="abs flbl" style="left:256px;top:523px">Express Service</div>
  <div class="abs select" style="left:256px;top:536px;width:154px"></div>
  <div class="abs flbl" style="left:256px;top:563px">FOB</div>
  <div class="abs select" style="left:256px;top:576px;width:154px"></div>
  <div class="abs flbl" style="left:256px;top:604px">Order Ship Rule</div>
  <div class="abs select" style="left:256px;top:617px;width:226px">Partials</div>
  <div class="abs req" style="left:489px;top:619px">*</div>
  <div class="abs flbl" style="left:256px;top:645px">Line Ship Rule</div>
  <div class="abs select" style="left:256px;top:658px;width:226px">Partials</div>
  <div class="abs req" style="left:489px;top:662px">*</div>

  <div class="abs flbl" style="left:534px;top:443px">Request Date</div>
  <div class="abs plain" style="left:534px;top:456px;width:136px"></div>
  <svg class="abs" style="left:674px;top:455px" width="21" height="21" viewBox="0 0 21 21"><rect x="1" y="3" width="19" height="17" rx="1.5" fill="var(--blue)"/><rect x="5" y="0.5" width="2" height="4" fill="var(--blue)"/><rect x="14" y="0.5" width="2" height="4" fill="var(--blue)"/><g fill="#fff"><rect x="3.5" y="8" width="3" height="2.5"/><rect x="7.5" y="8" width="3" height="2.5"/><rect x="11.5" y="8" width="3" height="2.5"/><rect x="15.5" y="8" width="2.5" height="2.5"/><rect x="3.5" y="12" width="3" height="2.5"/><rect x="7.5" y="12" width="3" height="2.5"/><rect x="11.5" y="12" width="3" height="2.5"/><rect x="15.5" y="12" width="2.5" height="2.5"/><rect x="3.5" y="16" width="3" height="2.2"/><rect x="7.5" y="16" width="3" height="2.2"/><rect x="11.5" y="16" width="3" height="2.2"/></g></svg>
  <div class="abs flbl" style="left:534px;top:483px">Freight Terms</div>
  <div class="abs select" style="left:534px;top:496px;width:160px">Collect</div>
  <div class="abs flbl" style="left:534px;top:523px">Freight Calc</div>
  <div class="abs select" style="left:534px;top:536px;width:160px"></div>

  <div class="abs flbl" style="left:794px;top:443px">Customer Ship To</div>
  <div class="abs grey" style="left:794px;top:456px;width:88px"></div>
  <div class="abs slash" style="left:892px;top:456px">/</div>
  <div class="abs grey" style="left:906px;top:456px;width:38px"></div>
</main>

<footer>
  <div class="abs status"></div>
  <div class="abs status-strip"></div>
  <div class="abs status-text">Enter property values, and click
    <svg width="13" height="10" viewBox="0 0 13 10" style="margin-left:4px"><path d="M1 5l3.5 3.5L12 1" fill="none" stroke="#3dbb6c" stroke-width="1.8"/></svg>Apply</div>
</footer>

</body>
</html>
```